Roofing Company Realtor Marketing Flyer

We would like a design for marketing material aimed at realtors. We are seeking to build relationships with local realtors to ensure that both sellers and buyers are happy and confident with their roofing systems through roof inspections, No-Leak certification, roof repairs, and replacements if necessary.

There are three points that must be included:
1. Home inspectors are generalists. We are roof experts that specialize in diagnosing and fixing roofing problems.
2. We offer "No Leak" certification to offer peace of mind to homeowners.
3. We offer referral bonuses for realtors.

Target Market(s)

Realtors

Industry/Entity Type

Roofing

Font styles to use
Sans Serif

Colors

Designer to choose colors to be used in the design.

Requirements
Must have
• Must be double-sided.
• Must be similar to current marketing materials design. See website http://gablecrestpro.example and attached images for details.
• We would also like a "fanned out" version of our Sample Inspection Report showing glimpses of some of the images on the later pages (See attached documents).

```html
<!DOCTYPE html>
<html lang="en">
<head>
<meta charset="utf-8">
<title>GableCrest Realtor Flyer</title>
<link href="https://fonts.googleapis.com/css2?family=Lato:wght@400;700&family=Orbitron:wght@700&family=Roboto:wght@500;700&display=swap" rel="stylesheet">
<style>
:root{
  --orange:#f0851c;
  --orange-deep:#e06f14;
  --dark:#262626;
  --ink:#222;
  --grey-panel:#efefef;
  --page:#e8e5e1;
  --white:#fff;
}
*{box-sizing:border-box;margin:0;padding:0}
html,body{width:1200px;height:1200px;overflow:hidden;background:var(--page);font-family:"Lato",sans-serif;color:var(--ink)}
.flyer{position:absolute;top:261px;width:525px;height:679px;box-shadow:0 6px 18px rgba(0,0,0,.35);overflow:hidden;background:var(--white)}
.flyer--front{left:47px}
.flyer--back{left:629px}
.sheet{position:absolute;left:0;top:0;width:656px;height:849px;transform:scale(.8);transform-origin:0 0}
.abs{position:absolute}
.header-art{position:absolute;left:0;top:0}
.brand{position:absolute;font-family:"Lato",sans-serif;font-weight:400;color:var(--orange);font-size:46px;letter-spacing:.5px;white-space:nowrap}
.headline{position:absolute;left:341px;top:142px;font-family:"Orbitron",sans-serif;font-weight:700;font-size:21px;line-height:28px;letter-spacing:1px}
.headline .dark{color:var(--dark)}
.headline .accent{color:var(--orange)}
.value-band{position:absolute;left:0;top:459px;width:656px;height:74px;background:linear-gradient(90deg,var(--orange-deep),var(--orange) 50%,var(--orange-deep));text-align:center;font-family:"Roboto",sans-serif;font-weight:700;font-size:24px;line-height:33px;padding-top:4px}
.value-band .lead{color:var(--dark);font-weight:500}
.value-band .strong{color:var(--white)}
.thumb{position:absolute;width:142px;height:118px;border:2px solid #cfcfcf;box-shadow:0 2px 4px rgba(0,0,0,.35)}
.thumb--shingle{background:linear-gradient(160deg,#9c6a45,#6e4a32 60%,#b28a5e)}
.thumb--leak{background:linear-gradient(170deg,#5a5a5a,#8a8580 55%,#3c3c3c)}
.thumb--replace{background:linear-gradient(180deg,#8fb6dc,#bcd4ea 55%,#e9eef2)}
.thumb--ladder{background:linear-gradient(150deg,#b79b77,#a33a2c 50%,#7e6a52)}
.thumb--nailer{background:linear-gradient(170deg,#6d6d6d,#4d4038 55%,#8a7868)}
.thumb--tile{background:linear-gradient(160deg,#3d7fc4,#c96a45 45%,#d9a17c)}
.caption{position:absolute;width:190px;text-align:center;font-size:13px;line-height:16px;color:var(--ink)}
.check-panel{position:absolute;left:0;top:719px;width:656px;height:62px;background:var(--grey-panel);font-size:10px;line-height:13px}
.check{position:absolute;display:flex;gap:8px;align-items:flex-start}
.check svg{flex:none;margin-top:1px}
.cta{position:absolute;left:0;top:790px;width:656px;text-align:center;color:var(--orange-deep);font-weight:700;font-size:14px}
.footer{position:absolute;left:0;top:817px;width:656px;height:32px;background:var(--dark);color:var(--white);font-size:10.5px;display:flex;justify-content:center;align-items:center;gap:20px}
.footer span{display:flex;align-items:center;gap:7px}
.photo{position:absolute}
.point-title{position:absolute;width:200px;text-align:center;font-weight:700;font-size:12.5px;line-height:15px;color:var(--ink)}
.point-body{position:absolute;width:164px;font-size:9px;line-height:11.5px;text-align:justify;color:#333}
.expert-line{position:absolute;left:278px;top:720px;font-weight:700;font-size:14px;display:flex;align-items:center;gap:9px;white-space:nowrap}
.badge-band{position:absolute;left:0;top:750px;width:656px;height:67px;background:var(--orange)}
.badge{position:absolute;top:8px;width:52px;height:52px;border-radius:50%;border:3px solid #fff;box-shadow:0 1px 3px rgba(0,0,0,.3)}
.badge--green{background:#5a9b3a}
.badge--blue{background:#2b5a9c}
.badge--red{background:#a33a2e}
.badge--bronze{background:#c88a3a}
</style>
</head>
<body>

<!-- Front side -->
<section class="flyer flyer--front">
  <div class="sheet">
    <svg class="header-art" width="656" height="460" viewBox="0 0 656 460" aria-hidden="true">
      <rect width="656" height="460" fill="#262626"/>
      <polygon points="0,148 177,34 336,131 656,131 656,460 0,460" fill="#9fc3e6"/>
      <polyline points="4,146 177,24 339,124 656,124" fill="none" stroke="#f0851c" stroke-width="13"/>
    </svg>
    <div class="photo" role="img" aria-label="Large two-storey brick house with a shingle roof under a blue sky with clouds, green lawn in front"
      style="left:0;top:240px;width:656px;height:219px;background:linear-gradient(180deg,rgba(159,195,230,0),#c9bfa9 30%,#bfb196 70%,#5f8a3c)"></div>
    <div class="brand" style="left:336px;top:24px">GableCrest</div>
    <div class="headline"><div class="dark">BUYING OR</div><div class="accent">SELLING A HOUSE?</div></div>

    <div class="value-band"><div class="lead">We can help protect your</div><div class="strong">INTERESTS &amp; ADD PROPERTY VALUE</div></div>

    <div class="thumb thumb--shingle" style="left:56px;top:549px" role="img" aria-label="Roofer in a hard hat inspecting a shingle roof ridge"></div>
    <div class="thumb thumb--leak" style="left:254px;top:549px" role="img" aria-label="Worker standing on a damaged shingle roof"></div>
    <div class="thumb thumb--replace" style="left:454px;top:549px" role="img" aria-label="Crew installing a new roof on a gable"></div>
    <div class="caption" style="left:32px;top:677px">Roof Analysis &amp;<br>NO-LEAK Certification</div>
    <div class="caption" style="left:230px;top:677px">Leak &amp;<br>Damage Repair</div>
    <div class="caption" style="left:430px;top:677px">Roof Replacement</div>

    <div class="check-panel">
      <div class="check" style="left:34px;top:13px"><svg width="11" height="11" viewBox="0 0 11 11"><rect x=".5" y=".5" width="10" height="10" fill="none" stroke="#f0851c"/><path d="M2.5 5.5l2 2 4-5" fill="none" stroke="#f0851c" stroke-width="1.4"/></svg>Understand the true detail of the roof.</div>
      <div class="check" style="left:34px;top:39px"><svg width="11" height="11" viewBox="0 0 11 11"><rect x=".5" y=".5" width="10" height="10" fill="none" stroke="#f0851c"/><path d="M2.5 5.5l2 2 4-5" fill="none" stroke="#f0851c" stroke-width="1.4"/></svg>Cover warranty gaps with our "No-Leak" Certification.</div>
      <div class="check" style="left:338px;top:13px;width:290px"><svg width="11" height="11" viewBox="0 0 11 11"><rect x=".5" y=".5" width="10" height="10" fill="none" stroke="#f0851c"/><path d="M2.5 5.5l2 2 4-5" fill="none" stroke="#f0851c" stroke-width="1.4"/></svg><span>Our expert crews perform the repair and replacement services.</span></div>
    </div>

    <div class="cta">Ask us about our partnership program!</div>

    <div class="footer">
      <span><svg width="11" height="11" viewBox="0 0 12 12"><path d="M2.5 1l2 2.5-1 1.5c.8 1.6 1.9 2.7 3.5 3.5l1.5-1 2.5 2-1.2 1.5C5.5 10.5 1.5 6.5 1 2.2z" fill="#f0851c"/></svg>844-GableCrest</span>
      <span><svg width="11" height="8" viewBox="0 0 11 8"><rect width="11" height="8" fill="#f0851c"/><path d="M0 0l5.5 4.5L11 0" fill="none" stroke="#262626"/></svg>info@gablecrestpro.example</span>
      <span><svg width="11" height="11" viewBox="0 0 12 12"><circle cx="6" cy="6" r="5.5" fill="#f0851c"/><path d="M.5 6h11M6 .5c-3 3-3 8 0 11M6 .5c3 3 3 8 0 11" fill="none" stroke="#262626" stroke-width=".8"/></svg>www.gablecrestpro.example</span>
    </div>
  </div>
</section>

<!-- Back side -->
<section class="flyer flyer--back">
  <div class="sheet">
    <svg class="header-art" width="656" height="400" viewBox="0 0 656 400" aria-hidden="true">
      <rect width="656" height="400" fill="#262626"/>
      <polygon points="0,138 345,138 478,38 656,166 656,400 0,400" fill="#8db7e2"/>
      <polyline points="0,130 342,130 478,27 658,157" fill="none" stroke="#f0851c" stroke-width="13"/>
    </svg>
    <div class="photo" role="img" aria-label="Two-storey stucco and stone house with a brown shingle roof, blue sky and green lawn"
      style="left:0;top:150px;width:656px;height:250px;background:linear-gradient(180deg,rgba(141,183,226,0),#c8b8ac 30%,#b9a89a 75%,#6f9a48)"></div>
    <div class="brand" style="left:29px;top:40px">GableCrest</div>

    <div class="thumb thumb--ladder" style="left:48px;top:416px" role="img" aria-label="Red ladder leaning against a roof edge among trees"></div>
    <div class="thumb thumb--nailer" style="left:254px;top:416px" role="img" aria-label="Roofer nailing shingles with a nail gun"></div>
    <div class="thumb thumb--tile" style="left:454px;top:416px" role="img" aria-label="Worker setting terracotta roof tiles"></div>

    <div class="point-title" style="left:27px;top:544px">Understand the true<br>detail of the roof</div>
    <div class="point-title" style="left:228px;top:544px">Cover warranty gaps with<br>our “No-Leak” Certification</div>
    <div class="point-title" style="left:430px;top:542px">Our expert crews<br>perform the repair<br>&amp; replacement services</div>

    <div class="point-body" style="left:49px;top:592px">Home inspectors, who are generalists, are often unable to adequately inspect and assess the condition of roofing systems. GableCrest's specialists are trained to diagnose roofing problems and recommend solutions to fit any budget. Our expert Advisors carefully investigate all aspects of the roofing system to assess the condition of the roof. After completing the inspection, our Advisors compile a comprehensive report of their findings including images of the roofing system.</div>
    <div class="point-body" style="left:246px;top:592px">Home warranties typically cover appliances, not roofing systems. What good is a warranty if it doesn't protect your property from top to bottom? Our "No-Leak" Certification provides peace of mind to homeowners</div>
    <div class="point-body" style="left:448px;top:592px">Repair and replacement services aren't just "jobs" to us. We take pride in every step of the process from quote to completion. Our dedicated office staff coordinates with our production team and technicians to ensure quality work and customer satisfaction.</div>

    <div class="expert-line">Speak With a Roofing Expert:
      <svg width="16" height="16" viewBox="0 0 12 12"><path d="M2.5 1l2 2.5-1 1.5c.8 1.6 1.9 2.7 3.5 3.5l1.5-1 2.5 2-1.2 1.5C5.5 10.5 1.5 6.5 1 2.2z" fill="#f0851c"/></svg>
      <span style="font-weight:400;font-size:15px">844-GableCrest</span>
    </div>

    <div class="badge-band">
      <div class="badge badge--green" style="left:67px"></div>
      <div class="badge badge--blue" style="left:194px"></div>
      <div class="badge badge--blue" style="left:313px"></div>
      <div class="badge badge--red" style="left:426px"></div>
      <div class="badge badge--bronze" style="left:541px"></div>
    </div>

    <div class="footer">
      <span><svg width="11" height="8" viewBox="0 0 11 8"><rect width="11" height="8" fill="#f0851c"/><path d="M0 0l5.5 4.5L11 0" fill="none" stroke="#262626"/></svg>info@gablecrestpro.example</span>
      <span><svg width="11" height="11" viewBox="0 0 12 12"><circle cx="6" cy="6" r="5.5" fill="#f0851c"/><path d="M.5 6h11M6 .5c-3 3-3 8 0 11M6 .5c3 3 3 8 0 11" fill="none" stroke="#262626" stroke-width=".8"/></svg>www.gablecrestpro.example</span>
    </div>
  </div>
</section>

</body>
</html>
```